Law Firm in Texas in need of new letterhead

Law Firm in Fort Worth, TX, USA named "Pell & Varnum, Attorneys-At-Law, LLP." This is a general practice law firm that mostly does Family Law and Criminal Defense work.

We are looking for a new letterhead that has a "classical" appeal, with modern elements.

Any color combination is fine, but please note that we do fax many documents, so the design must be clearly legible in Black and White.

We would like our letterhead to project a sense of professionalism, integrity, and ability.

Target Market(s)

Letterhead will be for correspondence generally with other attorneys and clients.

Industry/Entity Type

Law Firm

Logo Text

Pell & Varnum, Attorneys-At-Law, LLP.

Logo styles of interest
Pictorial/Combination Logo
Wordmark Logo
Lettermark Logo
Requirements
Nice to have
• Although not necessary, a "Texas Star" that is incorporated into the design would be a nice touch.
Should not have
• Colors that do not convert to B&W easily

```html
<!DOCTYPE html>
<html lang="en">
<head>
<meta charset="utf-8">
<title>Pell &amp; Varnum — Envelope Stationery</title>
<link rel="stylesheet" href="https://fonts.googleapis.com/css2?family=Cinzel:wght@400&family=Questrial&display=swap">
<style>
  :root {
    --canvas: #ebebeb;
    --paper: #f7f7f7;
    --paper-edge: #dcdcdc;
    --navy: #154a6e;
    --ghost: #e6e6e6;
    --on-navy: #f2f5f8;
  }
  * { margin: 0; padding: 0; box-sizing: border-box; }
  html, body {
    width: 1200px;
    height: 892px;
    overflow: hidden;
    background: var(--canvas);
  }
  .stationery {
    position: relative;
    width: 1200px;
    height: 892px;
  }
  .envelope {
    position: absolute;
    top: 316px;
    width: 520px;
    height: 260px;
    background: var(--paper);
    border: 1px solid var(--paper-edge);
    overflow: hidden;
  }
  .envelope--front { left: 50px; }
  .envelope--back { left: 630px; }

  .front__wordmark {
    position: absolute;
    left: 40px;
    top: 40px;
    color: var(--navy);
    font-family: "Cinzel", serif;
    font-weight: 400;
  }
  .front__name {
    font-size: 30px;
    line-height: 1;
    letter-spacing: 0.5px;
  }
  .front__descriptor {
    margin-top: 8px;
    font-size: 13px;
    letter-spacing: 1.6px;
    padding-left: 18px;
  }
  .front__address {
    position: absolute;
    left: 40px;
    top: 150px;
    font-family: "Questrial", sans-serif;
    font-size: 10px;
    color: var(--navy);
    letter-spacing: 0.2px;
  }
  .front__ghost-name {
    position: absolute;
    right: 24px;
    bottom: 22px;
    font-family: "Cinzel", serif;
    font-weight: 400;
    font-size: 46px;
    line-height: 1;
    color: var(--ghost);
    white-space: nowrap;
  }

  .back__flap {
    position: absolute;
    left: 0;
    top: 0;
    width: 100%;
    height: 92px;
    background: var(--navy);
    border-radius: 0 0 8px 8px;
    display: flex;
    align-items: center;
    justify-content: center;
  }
  .back__flap-name {
    font-family: "Cinzel", serif;
    font-weight: 400;
    font-size: 15px;
    letter-spacing: 1px;
    color: var(--on-navy);
  }
</style>
</head>
<body>
<main class="stationery">
  <section class="envelope envelope--front" aria-label="Envelope front">
    <div class="front__wordmark">
      <div class="front__name">Pell &amp; Varnum</div>
      <div class="front__descriptor">Attorneys-At-Law, LLP.</div>
    </div>
    <p class="front__address">1820 W Hollis Ave, Fort Worth, Texas 76104-215</p>
    <div class="front__ghost-name" aria-hidden="true">Pell &amp; Varnum</div>
  </section>

  <section class="envelope envelope--back" aria-label="Envelope back">
    <div class="back__flap">
      <span class="back__flap-name">Pell &amp; Varnum</span>
    </div>
  </section>
</main>
</body>
</html>
```